Elegant One-Page Flyer That Catches People's Eye

For a series of workshops and zoom calls I am marketing with a colleague of mine, we would like to have an elegant, catchy one-page flyer that entices people to contact us. I am envisioning a one-page flyer (a card that is somewhat larger than a postcard) with great text, layout and images which magnetically draws people to us and is positive and inspiring. Also, if at all possible, a QR code linking it to our websites. Good colours would be shades of blue and green. I am uploading: the Text, our pictures, logos and contact information.

```html
<!DOCTYPE html>
<html lang="en">
<head>
<meta charset="utf-8">
<title>Rising Above Hidden Career Deal Breakers</title>
<link rel="stylesheet" href="https://fonts.googleapis.com/css2?family=Poppins:wght@400;500;600;700&family=Bebas+Neue&display=swap">
<style>
  :root {
    --page: #ffffff;
    --card: #e7e7e7;
    --wine: #7b1416;
    --leaf: #89a862;
    --ink: #2f2f2f;
    --body: #262626;
    --pill-dark: #1d1d1d;
    --facilitator-bg: rgba(214,214,214,0.88);
  }
  * { box-sizing: border-box; margin: 0; padding: 0; }
  html, body { width: 1200px; height: 739px; overflow: hidden; background: var(--page); }
  body { font-family: "Poppins", sans-serif; color: var(--body); position: relative; }

  .flyer { position: absolute; left: 132px; top: 98px; width: 936px; height: 510px; background: var(--card); overflow: hidden; }

  .scenery {
    position: absolute; left: 516px; top: 0; width: 420px; height: 510px;
    background:
      linear-gradient(90deg, var(--card) 0%, rgba(231,231,231,0) 35%),
      linear-gradient(180deg, #b9c3c8 0%, #9aa6ab 35%, #6d6a63 65%, #3f3a35 100%);
  }

  .question { position: absolute; left: 40px; top: 30px; font-weight: 700; font-size: 18.5px; color: var(--wine); white-space: nowrap; }
  .question-sub { position: absolute; left: 41px; top: 53px; font-size: 12.6px; color: var(--ink); white-space: nowrap; }

  .title { position: absolute; left: 40px; top: 77px; font-weight: 700; font-size: 40px; line-height: 43px; white-space: nowrap; }
  .title .accent { color: var(--leaf); display: block; }
  .title .main { color: var(--ink); display: block; }

  .offer { position: absolute; left: 36px; top: 181px; width: 477px; height: 52px; border-radius: 26px; overflow: hidden; display: flex; }
  .offer-workshops { width: 224px; flex: none; background: var(--leaf); color: #fff; font-family: "Bebas Neue", sans-serif; font-size: 32px; line-height: 52px; padding-left: 10px; white-space: nowrap; }
  .offer-plus { position: absolute; left: 216px; top: 12px; color: #fff; font-weight: 700; font-size: 24px; line-height: 26px; }
  .offer-coaching { flex: 1; background: var(--wine); color: #fff; font-weight: 700; font-size: 13.2px; line-height: 16px; display: flex; align-items: center; padding-left: 22px; white-space: nowrap; }

  .learn { position: absolute; left: 45px; top: 249px; font-weight: 700; font-size: 13px; line-height: 15.6px; color: var(--wine); white-space: nowrap; }
  .topics { position: absolute; left: 44px; top: 276px; width: 471px; height: 77px; border: 1px dashed var(--leaf); border-top: none; border-radius: 0 0 8px 8px; }
  .topics::before { content: ""; position: absolute; left: 293px; top: -2px; width: 5px; height: 5px; border-radius: 50%; background: var(--leaf); }
  .topics::after { content: ""; position: absolute; left: 298px; right: -1px; top: 0; border-top: 1px dashed var(--leaf); }
  .topic { position: absolute; font-size: 9.8px; line-height: 12px; display: flex; gap: 6px; white-space: nowrap; }
  .topic svg { flex: none; margin-top: 2px; }

  .brand { position: absolute; white-space: nowrap; display: flex; align-items: center; gap: 8px; }
  .brand-one { left: 44px; top: 388px; font-size: 26px; color: var(--leaf); }
  .brand-one .dot { width: 14px; height: 14px; border-radius: 50%; background: var(--leaf); }
  .brand-two { left: 51px; top: 452px; font-size: 16px; color: var(--wine); letter-spacing: 0.5px; }

  .contact-lead { position: absolute; left: 251px; top: 371px; font-weight: 600; font-size: 12.4px; line-height: 14.5px; color: var(--body); white-space: nowrap; }
  .contact-name { position: absolute; left: 251px; font-weight: 700; font-size: 10.5px; line-height: 13px; white-space: nowrap; }
  .contact-name.one { top: 409px; color: var(--leaf); }
  .contact-name.two { top: 450px; color: var(--wine); }
  .contact-item { position: absolute; display: flex; align-items: center; gap: 6px; font-size: 11.2px; font-weight: 500; line-height: 14px; white-space: nowrap; }
  .contact-item.phone { left: 251px; }
  .contact-item.mail { left: 361px; }
  .row-one { top: 424px; }
  .row-two { top: 465px; }

  .facilitators-tag { position: absolute; left: 565px; top: 223px; width: 172px; height: 23px; background: var(--pill-dark); color: #fff; border-radius: 5px; font-size: 12px; font-weight: 600; letter-spacing: 5px; display: flex; align-items: center; padding-left: 14px; }

  .facilitator { position: absolute; left: 557px; width: 346px; height: 106px; border-radius: 53px; background: var(--facilitator-bg); border: 1.5px solid #222; }
  .facilitator.first { top: 259px; }
  .facilitator.second { top: 371px; }
  .portrait { position: absolute; left: 3px; top: 3px; width: 97px; height: 97px; border-radius: 50%; border: 2px solid #fff; }
  .portrait.a { background: linear-gradient(160deg, #d9d2cc, #9b8470 60%, #7d6a8c); }
  .portrait.b { background: linear-gradient(160deg, #f3f1ef, #c99a86 55%, #3a2c2a); }
  .facilitator-name { position: absolute; left: 113px; top: 12px; font-weight: 700; font-size: 14.5px; line-height: 18px; color: var(--wine); white-space: nowrap; }
  .facilitator-bio { position: absolute; left: 113px; top: 34px; font-size: 8.8px; line-height: 11.4px; color: var(--body); white-space: nowrap; }
  .second .facilitator-name { top: 18px; }
  .second .facilitator-bio { top: 41px; }
</style>
</head>
<body>
<main class="flyer">
  <div class="scenery" role="img" aria-label="Photo of a hiker standing on a rocky summit overlooking snowy mountain peaks"></div>

  <h2 class="question">IS YOUR CAREER GOING THE WAY YOU WANT?</h2>
  <p class="question-sub">If not, do you feel stuck? Blocked? Frustrated? Don’t know what to do about this?</p>

  <h1 class="title"><span class="accent">Rising Above Hidden</span><span class="main">Career Deal Breakers</span></h1>

  <div class="offer">
    <div class="offer-workshops">4 MINI-WORKSHOPS</div>
    <div class="offer-coaching">2 short Online Group Coaching<br>Sessions between Workshops</div>
    <div class="offer-plus">+</div>
  </div>

  <p class="learn">Learn to overcome and rise above<br>the 4 top hidden career deal breakers fast</p>
  <div class="topics">
    <div class="topic" style="left:14px;top:21px"><svg width="8" height="8" viewBox="0 0 8 8"><circle cx="4" cy="4" r="3.4" fill="none" stroke="#89a862" stroke-width="0.8"/><path d="M2.3 4.1l1.2 1.1 2.2-2.3" fill="none" stroke="#89a862" stroke-width="0.8"/></svg>Microaggressions</div>
    <div class="topic" style="left:196px;top:21px"><svg width="8" height="8" viewBox="0 0 8 8"><circle cx="4" cy="4" r="3.4" fill="none" stroke="#89a862" stroke-width="0.8"/><path d="M2.3 4.1l1.2 1.1 2.2-2.3" fill="none" stroke="#89a862" stroke-width="0.8"/></svg>Toxic black box team dynamics</div>
    <div class="topic" style="left:14px;top:44px"><svg width="8" height="8" viewBox="0 0 8 8"><circle cx="4" cy="4" r="3.4" fill="none" stroke="#89a862" stroke-width="0.8"/><path d="M2.3 4.1l1.2 1.1 2.2-2.3" fill="none" stroke="#89a862" stroke-width="0.8"/></svg><span>Workplace snakes and other<br>dysfunctional types</span></div>
    <div class="topic" style="left:196px;top:44px"><svg width="8" height="8" viewBox="0 0 8 8"><circle cx="4" cy="4" r="3.4" fill="none" stroke="#89a862" stroke-width="0.8"/><path d="M2.3 4.1l1.2 1.1 2.2-2.3" fill="none" stroke="#89a862" stroke-width="0.8"/></svg>Disempowering Subconscious Algorithms</div>
  </div>

  <div class="brand brand-one"><span class="dot"></span>NorthPath</div>
  <div class="brand brand-two">VennCoaching Basel</div>

  <p class="contact-lead">For dates, venue and further information<br>Contact Clara or Maren at</p>
  <p class="contact-name one">DR. MAREN HOLLOWAY</p>
  <span class="contact-item phone row-one"><svg width="9" height="9" viewBox="0 0 10 10"><path d="M2 1l2 2-1 1.2a6 6 0 0 0 2.8 2.8L7 6l2 2-1.4 1.4C4.5 9.4.6 5.5.6 2.4z" fill="#89a862"/></svg>076 555 0142</span>
  <span class="contact-item mail row-one"><svg width="11" height="8" viewBox="0 0 11 8"><rect width="11" height="8" fill="#89a862"/><path d="M0 0l5.5 4.3L11 0" fill="none" stroke="#e7e7e7" stroke-width="0.9"/></svg>maren@northpath.example</span>
  <p class="contact-name two">DR. CLARA VENN</p>
  <span class="contact-item phone row-two"><svg width="9" height="9" viewBox="0 0 10 10"><path d="M2 1l2 2-1 1.2a6 6 0 0 0 2.8 2.8L7 6l2 2-1.4 1.4C4.5 9.4.6 5.5.6 2.4z" fill="#7b1416"/></svg>079 555 01 87</span>
  <span class="contact-item mail row-two"><svg width="11" height="8" viewBox="0 0 11 8"><rect width="11" height="8" fill="#7b1416"/><path d="M0 0l5.5 4.3L11 0" fill="none" stroke="#e7e7e7" stroke-width="0.9"/></svg>clara@venncoaching.example</span>

  <div class="facilitators-tag">FACILITATORS</div>

  <section class="facilitator first">
    <div class="portrait a" role="img" aria-label="Portrait photo of Dr. Maren Holloway"></div>
    <h3 class="facilitator-name">Dr. Maren Holloway</h3>
    <p class="facilitator-bio">PhD, CPC, is an American &amp; Swiss-Trained<br>Work &amp; Organizational Psychologist,<br>ICF-Certified Coach, Board Certified<br>Hypnotherapist, Certified Naturopath (TEN)<br>&amp; Certified Ayurvedic Practitioner.</p>
  </section>

  <section class="facilitator second">
    <div class="portrait b" role="img" aria-label="Portrait photo of Dr. Clara Venn"></div>
    <h3 class="facilitator-name">Dr. Clara Venn</h3>
    <p class="facilitator-bio">Ph.D., PCC is a coach and somatic<br>experience practitioner, a team coach<br>with diploma and a certified virtual<br>team coach.</p>
  </section>
</main>
</body>
</html>
```